Marwick Law Letterhead

We need a new letterhead design for a Law Firm. The address for the law firm is 1475 Calloway Street, Suite 210, Houston, Texas 77041. Phone Number: 832-361-9027; Fax Number: 832-614-7359. The logo is uploaded to the project.

```html
<!DOCTYPE html>
<html lang="en">
<head>
<meta charset="utf-8">
<title>Marwick Law Letterhead</title>
<link rel="stylesheet" href="https://fonts.googleapis.com/css2?family=Libre+Caslon+Text&family=Montserrat:wght@400&display=swap">
<style>
  :root {
    --backdrop: #e8e8e8;
    --paper: #ffffff;
    --navy: #1c3160;
    --red: #d3222a;
    --faint-navy: #f2f3f7;
    --footer-text: #ffffff;
  }
  html, body {
    margin: 0;
    padding: 0;
    width: 1154px;
    height: 1200px;
    overflow: hidden;
    background: var(--backdrop);
  }
  .letterhead {
    position: absolute;
    left: 236px;
    top: 154px;
    width: 652px;
    height: 912px;
    background: var(--paper);
    overflow: hidden;
  }
  .brand {
    position: absolute;
    left: 24px;
    top: 66px;
    display: flex;
    align-items: center;
    gap: 10px;
  }
  .brand-dot {
    width: 14px;
    height: 14px;
    border-radius: 50%;
    background: var(--red);
  }
  .brand-name {
    font-family: "Libre Caslon Text", serif;
    font-size: 30px;
    line-height: 1;
    color: var(--navy);
    letter-spacing: 0.5px;
  }
  .backdrop-ring {
    position: absolute;
    left: 126px;
    top: 285px;
    width: 434px;
    height: 434px;
  }
  .contact-band {
    position: absolute;
    left: 0;
    top: 824px;
    width: 100%;
    height: 66px;
    background: var(--navy);
    color: var(--footer-text);
    font-family: "Montserrat", sans-serif;
    font-size: 11.5px;
    text-align: center;
  }
  .contact-numbers {
    position: absolute;
    top: 18px;
    left: 0;
    width: 100%;
    display: flex;
    justify-content: center;
    gap: 10px;
  }
  .contact-item {
    display: inline-flex;
    align-items: center;
    gap: 7px;
  }
  .contact-item svg { width: 11px; height: 11px; }
  .contact-address {
    position: absolute;
    top: 40px;
    left: 0;
    width: 100%;
  }
</style>
</head>
<body>
  <main class="letterhead">
    <header class="brand">
      <span class="brand-dot"></span>
      <span class="brand-name">Marwick Law</span>
    </header>

    <svg class="backdrop-ring" viewBox="0 0 434 434" aria-hidden="true">
      <circle cx="217" cy="217" r="190" fill="none" stroke="var(--faint-navy)" stroke-width="46"/>
    </svg>

    <footer class="contact-band">
      <div class="contact-numbers">
        <span class="contact-item">
          <svg viewBox="0 0 24 24" aria-hidden="true"><path fill="#fff" d="M6.6 10.8a15.1 15.1 0 0 0 6.6 6.6l2.2-2.2a1 1 0 0 1 1-.25 11.4 11.4 0 0 0 3.6.57 1 1 0 0 1 1 1V20a1 1 0 0 1-1 1A17 17 0 0 1 3 4a1 1 0 0 1 1-1h3.5a1 1 0 0 1 1 1c0 1.25.2 2.45.57 3.6a1 1 0 0 1-.25 1z"/></svg>
          832-361-9027
        </span>
        <span class="contact-item">
          <svg viewBox="0 0 24 24" aria-hidden="true"><path fill="#fff" d="M6 2h12v6H6zM4 9h16a2 2 0 0 1 2 2v6h-4v5H6v-5H2v-6a2 2 0 0 1 2-2zm4 7v4h8v-4z"/></svg>
          832-614-7359
        </span>
      </div>
      <div class="contact-address">1475 Calloway Street, Suite 210, Houston, Texas 77041</div>
    </footer>
  </main>
</body>
</html>
```